Professional and creative business card design for recruiting service providers

Our company supports German medium-sized companies in filling vacancies promptly. For this we use social media marketing and bring our customers into the visibility.

We want a professional but also creative design for our business cards.

Please look at lindqvar-staff.de to get an impression of our CI.

Target Market(s)

Small and medium-sized companies in Germany from the industry

Industry/Entity Type

Industrie, Handwerk

Contact Information for Business Card

Name, Position, Telefonnummer, Email, Website

Colors
EE7325
F08F49
F5BC92
FAE3D3
FDF4ED

Requirements
Must have
• A picture of the employee and in the style of www.lindqvar-staff.de

```html
<!DOCTYPE html>
<html lang="de">
<head>
<meta charset="utf-8">
<title>Lindqvar &amp; Staff – Visitenkarte</title>
<link rel="stylesheet" href="https://fonts.googleapis.com/css2?family=Montserrat:wght@600;700&family=Arimo:wght@400&display=swap">
<style>
  :root {
    --bg: #e9e9e9;
    --card-dark: #2f2f2f;
    --card-dark-2: #262626;
    --orange: #ee5a24;
    --white: #ffffff;
    --text-dark: #1f1f1f;
    --pattern-a: #3a3a3a;
    --pattern-b: #1c1c1c;
  }
  * { box-sizing: border-box; margin: 0; padding: 0; }
  html, body { width: 1200px; height: 802px; overflow: hidden; }
  body {
    background: var(--bg);
    position: relative;
    font-family: "Arimo", Arial, sans-serif;
  }
  .card {
    position: absolute;
    top: 226px;
    width: 540px;
    height: 350px;
    overflow: hidden;
    box-shadow: 0 6px 18px rgba(0,0,0,.18);
  }
  .card--front { left: 40px; background: var(--card-dark); }
  .card--back  { left: 620px; background: var(--card-dark-2); }

  /* front */
  .brand {
    position: absolute;
    left: 150px; top: 42px;
    display: flex; align-items: center; gap: 16px;
  }
  .brand__square { width: 54px; height: 54px; background: var(--orange); }
  .brand__name {
    font-family: "Montserrat", sans-serif;
    font-weight: 700;
    font-size: 27px;
    line-height: 1.02;
    letter-spacing: 1.5px;
    color: var(--white);
    text-transform: uppercase;
  }
  .person {
    position: absolute;
    right: 28px; top: 124px;
    text-align: right;
  }
  .person__name {
    font-family: "Montserrat", sans-serif;
    font-weight: 700;
    font-size: 21px;
    color: var(--orange);
    letter-spacing: .5px;
    text-transform: uppercase;
  }
  .person__role { font-size: 16px; color: var(--white); margin-top: 2px; }

  .photo {
    position: absolute;
    left: 0; bottom: 0;
    width: 270px; height: 210px;
    background: radial-gradient(ellipse at 45% 40%, #4a4640 0%, #232325 55%, #1b1b20 100%);
    z-index: 2;
  }
  .band { position: absolute; right: 0; left: 250px; }
  .band--contact { top: 188px; height: 82px; background: var(--white); padding: 9px 24px 0 0; }
  .band--address { top: 270px; bottom: 0; background: var(--orange); padding: 14px 24px 0 0; }
  .contact-line {
    display: flex; justify-content: flex-end; align-items: center; gap: 8px;
    font-size: 16px; color: var(--text-dark); line-height: 21px;
  }
  .contact-line svg { width: 13px; height: 13px; flex: none; }
  .address { text-align: right; color: var(--white); font-size: 17px; line-height: 23px; }

  /* back */
  .pattern {
    position: absolute; inset: 0;
    background: linear-gradient(135deg, var(--pattern-b) 0%, var(--pattern-a) 55%, #4a4a4a 100%);
  }
  .back-brand {
    position: absolute;
    left: 300px; top: 150px;
    display: flex; align-items: center; gap: 10px;
  }
  .back-brand__square { width: 30px; height: 30px; background: var(--orange); }
  .back-brand__name {
    font-family: "Montserrat", sans-serif;
    font-weight: 700; font-size: 15px; letter-spacing: 1px;
    color: var(--white); text-transform: uppercase; line-height: 1.05;
  }
</style>
</head>
<body>
  <section class="card card--front">
    <div class="brand">
      <div class="brand__square"></div>
      <div class="brand__name">Lindqvar<br>&amp; Staff</div>
    </div>

    <div class="person">
      <div class="person__name">Tobias Wendel</div>
      <div class="person__role">Manager</div>
    </div>

    <div class="band band--contact">
      <div class="contact-line">0171 394 2257
        <svg viewBox="0 0 24 24" aria-hidden="true"><path fill="#ee5a24" d="M6.6 10.8a15 15 0 0 0 6.6 6.6l2.2-2.2c.3-.3.7-.4 1-.2 1.1.4 2.3.6 3.6.6.6 0 1 .4 1 1V20c0 .6-.4 1-1 1C10.6 21 3 13.4 3 4c0-.6.4-1 1-1h3.5c.6 0 1 .4 1 1 0 1.3.2 2.5.6 3.6.1.3 0 .7-.2 1z"/></svg>
      </div>
      <div class="contact-line">info@lindqvar-staff.de
        <svg viewBox="0 0 24 24" aria-hidden="true"><rect x="3" y="5" width="18" height="14" rx="1.5" fill="none" stroke="#ee5a24" stroke-width="2.2"/><path d="M3.5 6l8.5 7 8.5-7" fill="none" stroke="#ee5a24" stroke-width="2.2"/></svg>
      </div>
      <div class="contact-line">www.lindqvar-staff.de
        <svg viewBox="0 0 24 24" aria-hidden="true"><circle cx="12" cy="12" r="9" fill="none" stroke="#ee5a24" stroke-width="2"/><path d="M3 12h18M12 3c3 3 3 15 0 18M12 3c-3 3-3 15 0 18" fill="none" stroke="#ee5a24" stroke-width="1.6"/></svg>
      </div>
    </div>

    <div class="band band--address">
      <div class="address">Bergstraße 27b<br>70180 Stuttgart</div>
    </div>

    <div class="photo" role="img" aria-label="Porträtfoto des Mitarbeiters in dunkler Kleidung vor dunklem Hintergrund"></div>
  </section>

  <section class="card card--back">
    <div class="pattern" role="img" aria-label="Geprägtes Wiederholungsmuster in Dunkelgrau über die ganze Kartenfläche"></div>
    <div class="back-brand">
      <div class="back-brand__square"></div>
      <div class="back-brand__name">Lindqvar<br>&amp; Staff</div>
    </div>
  </section>
</body>
</html>
```